New business card/stationary for a consulting company

I am looking for a clean and very professional looking business card for my consulting company as well as corresponding stationary. I am uploading our logo. I like simple and powerful for the feel. No graphics but I am open on everything else. Below is my contact information but would like the final to be in a version I can add my employees information into and print. Thank you.

Daniel Whitcombe
dan@ferncliffadvisory.com
2870 North 9th Avenue, Summit Floor, Elm Ridge, Illinois 60531
www.ferncliffadvisory.com

Industry/Entity Type

Consulting

Contact Information for Business Card

Daniel Whitcombe
dan@ferncliffadvisory.com
www.ferncliffadvisory.com

Font styles to use
Serif
Sans Serif

Requirements
Must have
• Our logo and the business card details.
Nice to have
• our website www.ferncliffadvisory.com

```html
<!DOCTYPE html>
<html lang="en">
<head>
<meta charset="utf-8">
<title>Ferncliff Advisory – Business Card</title>
<link rel="stylesheet" href="https://fonts.googleapis.com/css2?family=Questrial&family=PT+Sans:wght@400;700&display=swap">
<style>
  :root {
    --page-bg: #e6e7eb;
    --navy: #0e0e86;
    --navy-deep: #03035e;
    --royal: #1a1ab8;
    --paper: #fbfbfb;
    --ink: #4a4a4a;
    --white: #ffffff;
  }
  * { margin: 0; padding: 0; box-sizing: border-box; }
  html, body {
    width: 1200px; height: 900px; overflow: hidden;
    background: var(--page-bg);
  }
  .sheet {
    width: 1200px; height: 900px;
    display: flex; flex-direction: column; align-items: center; justify-content: center;
    gap: 40px;
  }
  .card {
    width: 700px; height: 400px; position: relative; overflow: hidden;
    box-shadow: 0 6px 18px rgba(0,0,0,0.18);
  }
  /* Front */
  .card-front {
    background: linear-gradient(110deg, var(--royal) 0%, var(--navy) 45%, var(--navy-deep) 100%);
    color: var(--white);
    display: flex; flex-direction: column; align-items: center; justify-content: center;
  }
  .brand {
    display: flex; align-items: center; gap: 16px;
    font-family: "Questrial", sans-serif; text-transform: uppercase;
    letter-spacing: 0.04em; line-height: 1;
  }
  .brand-square { display: block; flex: none; }
  .card-front .brand { font-size: 38px; color: var(--white); }
  .card-front .brand-square { width: 34px; height: 34px; background: var(--white); }
  .front-url {
    margin-top: 56px;
    font-family: "Questrial", sans-serif; font-size: 17px;
    letter-spacing: 0.42em; color: var(--white);
  }
  /* Back */
  .card-back { background: var(--paper); }
  .card-back .brand {
    position: absolute; top: 58px; right: 56px;
    font-size: 28px; color: var(--navy);
  }
  .card-back .brand-square { width: 26px; height: 26px; background: var(--navy); }
  .contact {
    position: absolute; left: 56px; bottom: 46px;
    font-family: "PT Sans", sans-serif; color: var(--ink);
  }
  .contact-name {
    font-weight: 700; font-size: 24px; color: var(--navy);
    text-transform: uppercase; letter-spacing: 0.01em; margin-bottom: 8px;
  }
  .contact-line { font-size: 15.5px; line-height: 1.45; }
  .contact-label { font-weight: 700; color: var(--navy); margin-right: 4px; }
  .contact-gap { display: inline-block; width: 14px; }
  .edge-bar {
    position: absolute; left: 0; bottom: 22px; width: 14px; height: 96px;
    background: var(--navy);
  }
  .edge-rule {
    position: absolute; left: 20px; bottom: 22px; width: 3px; height: 96px;
    background: var(--navy);
  }
</style>
</head>
<body>
<main class="sheet">
  <section class="card card-front" aria-label="Business card front">
    <div class="brand"><span class="brand-square"></span><span>Ferncliff Advisory</span></div>
    <p class="front-url">www.ferncliffadvisory.com</p>
  </section>

  <section class="card card-back" aria-label="Business card back">
    <div class="brand"><span class="brand-square"></span><span>Ferncliff Advisory</span></div>
    <div class="edge-bar"></div>
    <div class="edge-rule"></div>
    <div class="contact">
      <h1 class="contact-name">Daniel Whitcombe</h1>
      <p class="contact-line">2870 North 9th Avenue, Summit Floor, Elm Ridge, Illinois 60531</p>
      <p class="contact-line">
        <span class="contact-label">E:</span>dan@ferncliffadvisory.com<span class="contact-gap"></span>
        <span class="contact-label">W:</span>ferncliffadvisory.com
      </p>
    </div>
  </section>
</main>
</body>
</html>
```